BrivoTerna. Lantern of the Steady Harvest. Business card

Professional business card for BrivoTerna (Lantern of the Steady Harvest)
My rationale: Strategy-> Execution-> Results-> Value that lead to the BrivoTerna name: We put the Lantern of the Steady Harvest.
We deliver value to our customers helping them at defining a good strategy (cyan arrow). 90% of well formulated strategies fail due to poor execution so we also consider strategical execution very important (green arrow). Due to the execution we obtain the results (blue arrow). Finally, the results provide feedback to redefine strategy, and the new strategy has to be executed and new results obtained providing new feedback and on and on. It's like a wheel that finally, must create corporate value: value for shareholders, staholders, employees, providers...-

Target Market(s)

CEOs and steering comitees , invewrnent funds

Industry/Entity Type

Business Consultant

Contact Information for Business Card

Teodoro Vinsquel
CEO & Founder
teodoro.vinsquel@brivoterna-example.com
Mobile: +34 655.803.912
www.brivoterna-example.com

Colors

Designer to choose colors to be used in the design.

Requirements
Nice to have
• Nice to hace the words: Strategy, execution, results
• Nice to vave the claim: Lantern of the Steady Harvest
• The three colors should be shown:
• cyan for STRATEGY
• green for EXECUTION
• blue for RESULTS
Should not have
• Complete black background

```html
<!DOCTYPE html>
<html lang="en">
<head>
<meta charset="utf-8">
<title>BrivoTerna — Business Card</title>
<link rel="stylesheet" href="https://fonts.googleapis.com/css2?family=Roboto:wght@400;700&display=swap">
<style>
  :root {
    --stage: #2b2c2f;
    --card-white: #ffffff;
    --card-dark: #1d1e21;
    --pattern-tone: #2e2f33;
    --navy: #0b2a8f;
    --cyan: #1ba6ea;
    --green: #8cc63f;
    --ink-blue: #2a4fb8;
    --text-dark: #2c2f3a;
  }
  * { box-sizing: border-box; margin: 0; padding: 0; }
  html, body { width: 1200px; height: 1108px; overflow: hidden; }
  body {
    background: var(--stage);
    font-family: "Roboto", Arial, sans-serif;
    position: relative;
  }
  .card {
    position: absolute;
    top: 229px;
    width: 410px;
    height: 650px;
    border-radius: 30px;
    overflow: hidden;
  }
  .card--front {
    left: 160px;
    background: var(--card-white);
    text-align: center;
  }
  .card--back {
    left: 630px;
    background: var(--card-dark);
  }
  .brand {
    position: absolute;
    top: 170px;
    left: 0; right: 0;
    display: flex;
    align-items: center;
    justify-content: center;
    gap: 14px;
  }
  .brand__dot {
    width: 26px; height: 26px;
    border-radius: 50%;
    background: var(--green);
  }
  .brand__name {
    font-weight: 700;
    font-size: 54px;
    letter-spacing: -1px;
    color: var(--navy);
  }
  .person {
    position: absolute;
    top: 378px;
    left: 0; right: 0;
  }
  .person__name {
    font-weight: 700;
    font-size: 25px;
    color: var(--cyan);
  }
  .person__title {
    margin-top: 4px;
    font-size: 16px;
    color: var(--text-dark);
  }
  .divider {
    position: absolute;
    top: 452px;
    left: 60px; right: 60px;
    height: 30px;
  }
  .contact {
    position: absolute;
    top: 500px;
    left: 0; right: 0;
    font-size: 17px;
    line-height: 24px;
    color: var(--ink-blue);
  }
  .back-pattern {
    position: absolute;
    inset: 0;
    background: linear-gradient(160deg, var(--pattern-tone), var(--card-dark) 75%);
  }
  .back-brand {
    position: absolute;
    right: 40px;
    top: 440px;
    font-weight: 700;
    font-size: 24px;
    color: var(--cyan);
  }
</style>
</head>
<body>
  <section class="card card--front" aria-label="Business card front">
    <div class="brand">
      <span class="brand__dot"></span>
      <span class="brand__name">BrivoTerna</span>
    </div>
    <div class="person">
      <p class="person__name">Teodoro Vinsquel</p>
      <p class="person__title">CEO &amp; Founder</p>
    </div>
    <svg class="divider" viewBox="0 0 290 30" aria-hidden="true">
      <line x1="0" y1="15" x2="290" y2="15" stroke="#2a4fb8" stroke-width="1.2"/>
      <g>
        <circle cx="117" cy="15" r="13" fill="#1ba6ea"/>
        <path d="M111 10 q2 -2 4 0 l1 3 -2 1 q1 3 4 4 l1 -2 3 1 q2 2 0 4 q-9 0 -11 -11z" fill="#fff"/>
        <circle cx="145" cy="15" r="13" fill="#1ba6ea"/>
        <rect x="138" y="10" width="14" height="10" rx="1" fill="#fff"/>
        <path d="M138 10 l7 6 7 -6" fill="none" stroke="#1ba6ea" stroke-width="1.4"/>
        <circle cx="173" cy="15" r="13" fill="#1ba6ea"/>
        <circle cx="173" cy="15" r="7" fill="none" stroke="#fff" stroke-width="1.6"/>
        <line x1="166" y1="15" x2="180" y2="15" stroke="#fff" stroke-width="1.4"/>
        <ellipse cx="173" cy="15" rx="3" ry="7" fill="none" stroke="#fff" stroke-width="1.4"/>
      </g>
    </svg>
    <div class="contact">
      <p>+34 655.803.912</p>
      <p>www.brivoterna-example.com</p>
      <p>teodoro.vinsquel@brivoterna-example.com</p>
    </div>
  </section>

  <section class="card card--back" aria-label="Business card back">
    <div class="back-pattern" role="img" aria-label="Faint repeating brand pattern across the dark card back"></div>
    <span class="back-brand">BrivoTerna</span>
  </section>
</body>
</html>
```